Corvane Capital Business Cards

These are professional business cards that are for my family office.
Put fake emails and phone numbers as of now until I finalize those components. This family office controls my families investments, assets, and future. The cards should be professional.
..
.
.
.
I just uploaded another variation of a logo I would like to see as a business card to I am inbeteen which logo to use

Target Market(s)

business

Industry/Entity Type

business

Contact Information for Business Card

Professional, wealth related, finance related.

Requirements
Must have
• Logo

```html
<!DOCTYPE html>
<html lang="en">
<head>
<meta charset="UTF-8">
<title>Corvane Capital – Business Card</title>
<link href="https://fonts.googleapis.com/css2?family=Montserrat:wght@400;600;700&display=swap" rel="stylesheet">
<style>
  :root {
    --ink: #1b1f2b;
    --text: #2a2d35;
    --card: #ffffff;
    --backdrop: #1d1d1f;
  }
  html, body {
    margin: 0;
    padding: 0;
    width: 1200px;
    height: 1059px;
    overflow: hidden;
    background: var(--backdrop);
  }
  .business-card {
    position: absolute;
    left: 50px;
    top: 216px;
    width: 1100px;
    height: 627px;
    background: var(--card);
    border-radius: 32px;
    overflow: hidden;
    font-family: "Montserrat", sans-serif;
    color: var(--text);
    box-shadow: 0 18px 40px rgba(0,0,0,0.45);
  }
  .business-card > * {
    position: absolute;
    margin: 0;
    line-height: 1;
    white-space: nowrap;
  }
  .brand-wordmark {
    left: 47px;
    top: 56px;
    font-size: 61px;
    font-weight: 600;
    letter-spacing: 1px;
    color: var(--ink);
    text-transform: uppercase;
  }
  .brand-circle {
    left: 822px;
    top: 38px;
    width: 174px;
    height: 174px;
  }
  .brand-secondary {
    right: 42px;
    top: 234px;
    font-size: 27px;
    font-weight: 600;
    letter-spacing: 1.5px;
    color: var(--ink);
    text-transform: uppercase;
  }
  .name-accent {
    left: 0;
    top: 319px;
    width: 32px;
    height: 89px;
    background: var(--ink);
  }
  .holder-name {
    left: 47px;
    top: 312px;
    font-size: 54px;
    font-weight: 700;
    color: var(--ink);
    letter-spacing: 0.5px;
  }
  .holder-title {
    left: 47px;
    top: 376px;
    font-size: 29px;
    font-weight: 400;
    letter-spacing: 0.5px;
  }
  .divider {
    left: 47px;
    top: 438px;
    width: 1011px;
    height: 3px;
    background: var(--ink);
  }
  .contact-line {
    left: 47px;
    font-size: 28px;
    font-weight: 400;
    display: flex;
    align-items: center;
    gap: 12px;
  }
  .contact-line svg {
    width: 24px;
    height: 24px;
    fill: var(--ink);
    flex: none;
  }
  .contact-phone { top: 467px; }
  .contact-email { top: 510px; }
  .contact-web { top: 554px; }
  .address-line {
    right: 42px;
    font-size: 28px;
    font-weight: 400;
    text-align: right;
  }
  .address-street { top: 518px; }
  .address-region { top: 561px; }
</style>
</head>
<body>
  <div class="business-card">
    <p class="brand-wordmark">Corvane Capital</p>

    <svg class="brand-circle" viewBox="0 0 174 174" aria-hidden="true">
      <circle cx="87" cy="87" r="84" fill="none" stroke="#1b1f2b" stroke-width="4"/>
    </svg>
    <p class="brand-secondary">Corvane Capital</p>

    <div class="name-accent"></div>
    <h1 class="holder-name">DANIEL HALE</h1>
    <p class="holder-title">Managing Director</p>

    <div class="divider"></div>

    <p class="contact-line contact-phone">
      <svg viewBox="0 0 24 24" aria-hidden="true"><path d="M2 9c0-3 5-5 10-5s10 2 10 5v2h-5V9c-1-.6-3-1-5-1s-4 .4-5 1v2H2V9zm4 3h12l3 7H3l3-7zm6 1.5a2.5 2.5 0 1 0 0 5 2.5 2.5 0 0 0 0-5z"/></svg>
      <span>123 456 789</span>
    </p>
    <p class="contact-line contact-email">
      <svg viewBox="0 0 24 24" aria-hidden="true"><path d="M3 6h18v1.5l-9 6-9-6V6zm0 3.8 9 6 9-6V18H3V9.8z"/></svg>
      <span>info@yourgmail.com</span>
    </p>
    <p class="contact-line contact-web">
      <svg viewBox="0 0 24 24" aria-hidden="true"><path d="M12 2a10 10 0 1 0 0 20 10 10 0 0 0 0-20zm-1 2.1V7l-3 2-1 3 2 2v3l2 2.9A8 8 0 0 1 11 4.1zm2 15.8V17l3-2 1-3-2-1h-3l-1-2 3-2 1-3a8 8 0 0 1-2 15.9z"/></svg>
      <span>www.yourwebsite.com</span>
    </p>

    <p class="address-line address-street">Your address, City</p>
    <p class="address-line address-region">State, Zip 1234</p>
  </div>
</body>
</html>
```